Business Card Design

I need a logo and a business card design that can be used for my business stationary, Facebook page and in the future a website. I don't know if I need a large design for brochures and stationery and a small portion of that as the logo or business card design. I probably need some advice about that. My new company is called Willowbank Family Circle. I don't have all of my business contact details available yet, but I want to get the design ready, so that when all this information is available I can get the printing done quickly.I'm a social worker and my business will be providing parenting groups and counselling sessions for parents.I would like the logo and business card to be very feminine and pretty. I want a silhouette image of a Mother and Baby and decorative swirls of flowers/vines/leaves and butterflies.I have found some designs elsewhere that are along the lines of what I am looking for. These images are attached below, but the quality of these attachments is very poor as I photographed them with my phone.My preferred colours would be to use black and white, purple and/or pink, aqua and or blue/green.There are four logo/business card options attached. Logo option 1 - I really like the flower and vine design. Logo option 2 - again I like the flowers and leaf design and the use of colour and the silhouette image of the Mum and Baby; Logo option 3 - I like the butterflies and decorative swirls in this option and Logo option 4 - I think this design is the best for a logo. I love the mother and baby image. I don't like the tree branch and the birds but I like the way the hair has been incorporated into the branch. I prefer the design of the flowers/vine/leaves in the other options.

Industry/Entity Type

Business

Contact Information for Business Card

Company Name:Embrace Attachment ParentingMobile:0417 751 394Email:Currently sourcing - TBAContact Name:Janelle ApplegarthQualifications:Currently sourcing details - TBA

Font styles to use
Script

Colors
33a6d7
85cae6
886aae
6c459b
e667a6
eea4c8

Requirements
Must have
• My project must have an image of a mother and child, slightly encircled by the mother's hair perhaps in a heart shape, and the mother's hair becoming a beautiful filigree design of vine/leaves/flowers and with some butterfly somewhere.
• Can all of the Words be in the same font Attachment Parenting can be slightly smaller.
Nice to have
• I would like to also have a similar vine/leaves/flowers and maybe a butterfly on the opposite side of the card. Maybe the Mother/child image on the top left of the card and the other pattern on the bottom right.
• If possible the use of aqua, purple and pink.

```html
<!DOCTYPE html>
<html lang="en">
<head>
<meta charset="utf-8">
<title>Willowbank Family Circle – Business Card</title>
<link rel="stylesheet" href="https://fonts.googleapis.com/css2?family=Open+Sans:wght@400;600&display=swap">
<style>
  :root {
    --teal-deep: #0f7080;
    --teal-bright: #149aa3;
    --teal-line: #1aa0a8;
    --purple: #a148f0;
    --ink: #3a3a3a;
    --mist: #dbeaed;
    --paper: #ffffff;
  }
  html, body {
    margin: 0;
    padding: 0;
    width: 1200px;
    height: 686px;
    overflow: hidden;
    background: var(--paper);
  }
  .card {
    position: relative;
    width: 1200px;
    height: 686px;
    box-sizing: border-box;
    border: 1px solid var(--teal-line);
    background: var(--paper);
    overflow: hidden;
    font-family: "Open Sans", Arial, sans-serif;
  }
  .brand-mark {
    position: absolute;
    left: 255px;
    top: 30px;
    width: 180px;
    height: 180px;
    border-radius: 50%;
    background: var(--teal-deep);
  }
  .brand-name {
    position: absolute;
    left: 0;
    width: 662px;
    top: 262px;
    margin: 0;
    text-align: center;
    color: var(--teal-deep);
    font-weight: 600;
    font-size: 54px;
    line-height: 62px;
  }
  .brand-rule {
    position: absolute;
    left: 0;
    top: 420px;
    width: 637px;
    height: 7px;
    background: var(--teal-bright);
  }
  .contact {
    position: absolute;
    left: 34px;
    display: flex;
    align-items: center;
    color: var(--ink);
    font-size: 26px;
  }
  .contact svg { width: 48px; height: 40px; flex: none; }
  .contact span { margin-left: 54px; }
  .contact-email { top: 463px; }
  .contact-phone { top: 553px; }
  .backdrop-disc {
    position: absolute;
    left: 700px;
    top: 140px;
    width: 480px;
    height: 480px;
    border-radius: 50%;
    background: var(--mist);
    opacity: 0.55;
  }
  .person {
    position: absolute;
    left: 700px;
    width: 480px;
    text-align: center;
    margin: 0;
  }
  .person-name {
    top: 342px;
    color: var(--purple);
    font-size: 50px;
    font-weight: 400;
    line-height: 60px;
  }
  .person-role {
    top: 408px;
    color: var(--teal-deep);
    font-size: 21px;
    line-height: 28px;
    left: 685px;
  }
  .footer-band {
    position: absolute;
    left: 0;
    bottom: 0;
    width: 1200px;
    height: 47px;
  }
</style>
</head>
<body>
  <div class="card">
    <div class="brand-mark"></div>
    <h1 class="brand-name">Willowbank<br>Family Circle</h1>
    <div class="brand-rule"></div>

    <div class="contact contact-email">
      <svg viewBox="0 0 48 40" aria-hidden="true">
        <rect x="2" y="4" width="44" height="32" fill="var(--teal-bright)"/>
        <path d="M2 4 L24 24 L46 4" fill="none" stroke="#fff" stroke-width="2.5"/>
        <path d="M2 36 L18 19 M46 36 L30 19" fill="none" stroke="#fff" stroke-width="2"/>
      </svg>
      <span>Currently Sourcing</span>
    </div>

    <div class="contact contact-phone">
      <svg viewBox="0 0 48 40" aria-hidden="true">
        <path d="M10 2 L18 10 L13 16 C16 23 21 28 28 31 L34 26 L42 34 L36 40 C20 38 7 25 5 8 Z" fill="var(--teal-bright)"/>
      </svg>
      <span>0438 260 517</span>
    </div>

    <div class="backdrop-disc"></div>
    <p class="person person-name">Rosalind Thackeray</p>
    <p class="person person-role">(DIRECTOR)</p>

    <svg class="footer-band" viewBox="0 0 1200 47" preserveAspectRatio="none" aria-hidden="true">
      <polygon points="0,0 893,0 867,47 0,47" fill="var(--teal-deep)"/>
      <polygon points="912,0 1200,0 1200,47 887,47" fill="var(--purple)"/>
    </svg>
  </div>
</body>
</html>
```